MRT Property - Business Cards

Looking for a business card & general letterhead, signage etc design for our new logo.

Colours:
000a20
0056a2
00b5ef
0088ce
68cef2

Fonts:
Poppins
Karla

Please keep look and feel of new brand - example in the zip package I sent.

```html
<!DOCTYPE html>
<html lang="en">
<head>
<meta charset="utf-8">
<title>MRT Property Stationery</title>
<link rel="stylesheet" href="https://fonts.googleapis.com/css2?family=Poppins:wght@400;500;600&display=swap">
<style>
  :root {
    --ink: #000a20;
    --navy: #0056a2;
    --blue: #0088ce;
    --sky: #00b5ef;
    --light: #68cef2;
    --edge: #5bc2e7;
    --envelope: #5fbfe3;
    --envelope-flap: #6ac6e8;
    --paper: #ffffff;
    --card: #f3f4f5;
    --backdrop: #d4d4d4;
  }
  * { box-sizing: border-box; margin: 0; padding: 0; }
  html, body { width: 1200px; height: 686px; overflow: hidden; }
  body {
    background: var(--backdrop);
    font-family: "Poppins", sans-serif;
    position: relative;
  }
  .letterhead {
    position: absolute; left: 70px; top: 46px;
    width: 420px; height: 594px;
    background: var(--paper);
    border: 3px solid var(--edge);
  }
  .brand-name {
    font-family: "Poppins", sans-serif;
    font-weight: 600;
    color: var(--navy);
    display: flex; align-items: center; gap: 6px;
    white-space: nowrap;
  }
  .brand-dot { display: inline-block; border-radius: 50%; background: var(--sky); }
  .letterhead .brand-name { position: absolute; left: 34px; top: 42px; font-size: 22px; }
  .letterhead .brand-dot { width: 12px; height: 12px; }
  .letterhead-contact {
    position: absolute; left: 246px; top: 40px;
    padding-left: 12px;
    border-left: 1.5px solid var(--blue);
    font-size: 8.6px; line-height: 1.45;
    color: var(--ink);
  }
  .contact-line { display: flex; align-items: center; gap: 4px; white-space: nowrap; }
  .contact-line svg { width: 8px; height: 8px; flex: none; fill: var(--blue); }
  .contact-address { color: var(--blue); margin-top: 2px; }
  .contact-address .contact-line { align-items: flex-start; }
  .contact-address .indent { padding-left: 12px; }

  .envelope {
    position: absolute; left: 548px; top: 70px;
    width: 470px; height: 235px;
  }
  .card {
    position: absolute; left: 620px; top: 350px;
    width: 400px; height: 260px;
    background: var(--card);
    border: 3px solid var(--edge);
  }
  .card .brand-name { position: absolute; right: 26px; top: 30px; font-size: 18px; }
  .card .brand-dot { width: 10px; height: 10px; }
  .card-contact {
    position: absolute; right: 26px; top: 92px;
    font-size: 8.4px; line-height: 1.55; color: var(--ink);
    text-align: right;
  }
  .card-contact .contact-line { justify-content: flex-end; }
  .card-contact .gap { margin-top: 8px; }
</style>
</head>
<body>

<section class="letterhead">
  <div class="brand-name"><span class="brand-dot"></span>MRT Property</div>
  <div class="letterhead-contact">
    <div class="contact-line">
      <svg viewBox="0 0 10 10"><path d="M2 1h2l1 2.5-1.2.9a5 5 0 0 0 1.8 1.8l.9-1.2L9 6v2a1 1 0 0 1-1 1A7 7 0 0 1 1 2a1 1 0 0 1 1-1z"/></svg>
      +61 2 9000 4821
    </div>
    <div class="contact-line">
      <svg viewBox="0 0 10 10"><circle cx="5" cy="5" r="4.2" fill="none" stroke="currentColor" stroke-width="1.2" style="stroke:var(--blue)"/><path d="M1 5h8M5 1c-2 2.5-2 5.5 0 8M5 1c2 2.5 2 5.5 0 8" fill="none" style="stroke:var(--blue)" stroke-width=".9"/></svg>
      www.mrtproperty.com.au
    </div>
    <div class="contact-line">
      <svg viewBox="0 0 10 10"><rect x="0.5" y="2" width="9" height="6.5" rx="1"/><path d="M1 2.6l4 3 4-3" fill="none" stroke="#fff" stroke-width=".9"/></svg>
      info@mrtproperty.com.au
    </div>
    <div class="contact-address">
      <div class="contact-line">
        <svg viewBox="0 0 10 10"><path d="M5 .5a3.3 3.3 0 0 1 3.3 3.3C8.3 6.3 5 9.5 5 9.5S1.7 6.3 1.7 3.8A3.3 3.3 0 0 1 5 .5z"/><circle cx="5" cy="3.8" r="1.2" fill="#fff"/></svg>
        Suite 4.12, Tower 3
      </div>
      <div class="indent">18 Harbourline Road,</div>
      <div class="indent">Rivergate NSW 2150</div>
    </div>
  </div>
</section>

<svg class="envelope" viewBox="0 0 470 235" aria-label="Envelope back">
  <rect x="0" y="0" width="470" height="235" fill="var(--envelope)"/>
  <path d="M470 0 L470 235 L360 235 Q346 235 340 222 L262 30 Q254 12 272 8 L460 0 Z" fill="var(--envelope-flap)"/>
  <path d="M360 235 Q346 235 340 222 L262 30 Q254 12 272 8 L460 0" fill="none" stroke="#4fb0d6" stroke-width="1.5"/>
</svg>

<section class="card">
  <div class="brand-name"><span class="brand-dot"></span>MRT Property</div>
  <div class="card-contact">
    <div>Suite 4.12, Tower 3</div>
    <div>18 Harbourline Road,</div>
    <div>Rivergate NSW 2150</div>
    <div class="contact-line gap">+61 2 9000 4821
      <svg viewBox="0 0 10 10"><path d="M2 1h2l1 2.5-1.2.9a5 5 0 0 0 1.8 1.8l.9-1.2L9 6v2a1 1 0 0 1-1 1A7 7 0 0 1 1 2a1 1 0 0 1 1-1z"/></svg>
    </div>
    <div class="contact-line">www.mrtproperty.com.au
      <svg viewBox="0 0 10 10"><circle cx="5" cy="5" r="4.2" fill="none" style="stroke:var(--blue)" stroke-width="1.2"/><path d="M1 5h8M5 1c-2 2.5-2 5.5 0 8M5 1c2 2.5 2 5.5 0 8" fill="none" style="stroke:var(--blue)" stroke-width=".9"/></svg>
    </div>
    <div class="contact-line">info@mrtproperty.com.au
      <svg viewBox="0 0 10 10"><rect x="0.5" y="2" width="9" height="6.5" rx="1"/><path d="M1 2.6l4 3 4-3" fill="none" stroke="#fff" stroke-width=".9"/></svg>
    </div>
  </div>
</section>

</body>
</html>
```